Velour Detailing – Premium Automotive Detailing Studio Website Design

We're launching a premium automotive detailing studio called Velour Detailing, and we’re looking for a clean, minimal, and high-end website design (desktop + mobile version). The studio targets owners of luxury vehicles who care deeply about aesthetics, perfection, and exceptional service.
This project is about more than just showing services , it should feel like a luxury experience from the very first second. The design should be modern, minimalistic, elegant, and clearly aimed at an upscale market.
We’re looking for a designer who can translate our physical studio’s premium interior and architectural feel into a digital presence.
What we want the website to feel like:
Clean and modern
Professional and luxurious
Minimal and not cluttered
Light animations or transitions to add polish
Stylish and cinematic
Design freedom:
We trust your design direction. We are not providing strict color codes or layout instructions, we want you to create what you believe works best based on our brand positioning and target audience. Just keep it premium, modern, and well-organized.
What the website should include:
Hero section with a bold visual (image or video)
About the Studio — a few blocks explaining our story and focus on quality
Service Overview — clearly showing what we offer (detailing, ceramic coating, interior, etc.)
Gallery/Showcase — show off our work with cars, interior, and the space itself
Client Lounge Area — mention comfort, coffee, and waiting space
Testimonials — social proof from satisfied clients
Location & contact section — map, address, contact form
Footer, simple with nav, contact info, and optional social media
Target audience:
Owners of high-end vehicles (Valtrane, Korvel, etc.)
Car collectors and detailing enthusiasts
People looking for premium-level service and presentation
Brands/creators booking our photo studio

```html
<!DOCTYPE html>
<html lang="en">
<head>
<meta charset="utf-8">
<title>Velour Detailing – Premium Automotive Detailing</title>
<link href="https://fonts.googleapis.com/css2?family=Orbitron:wght@500;600;700&family=Montserrat:wght@400;500;600;700&display=swap" rel="stylesheet">
<style>
:root{
  --blue:#1f78c1;
  --blue-bright:#2a8ad8;
  --navy:#0f2d4c;
  --deep:#0b2744;
  --ice:#dcebf7;
  --ink:#151515;
  --text:#4a4a4a;
  --dark:#1d1d1d;
  --white:#ffffff;
}
*{margin:0;padding:0;box-sizing:border-box}
html,body{width:1200px;height:5319px;overflow:hidden}
body{position:relative;background:var(--white);font-family:'Montserrat',sans-serif;color:var(--ink)}
.abs{position:absolute}
.heading{font-family:'Orbitron',sans-serif;font-weight:600;letter-spacing:1px;color:var(--ink)}
.center{left:0;width:1200px;text-align:center}
.rule{position:absolute;height:4px;width:80px;background:var(--blue)}
.btn{position:absolute;display:flex;align-items:center;justify-content:center;font-size:14px;font-weight:700;color:var(--white);letter-spacing:.5px;background:var(--blue);clip-path:polygon(0 0,100% 0,calc(100% - 16px) 100%,0 100%)}
.btn-tail{position:absolute;width:12px;background:var(--blue);transform:skewX(-28deg)}
.photo{position:absolute}
.para{position:absolute;font-size:14px;line-height:29px;color:var(--text)}
/* header */
.brand{display:flex;align-items:center;gap:10px;font-family:'Montserrat',sans-serif;font-weight:700;font-size:22px;letter-spacing:2px;color:var(--ink)}
.brand-mark{width:26px;height:26px;background:var(--ink)}
.top-item{position:absolute;top:22px;display:flex;align-items:center;gap:8px;font-size:14px;color:var(--ink)}
.nav a{position:absolute;top:86px;font-size:14px;color:var(--ink);text-decoration:none}
.nav a.active{color:var(--blue);font-weight:600;border-bottom:2px solid var(--blue);padding-bottom:3px}
/* service cards */
.card{position:absolute;top:1455px;width:235px;height:285px;background:var(--white);box-shadow:0 2px 8px rgba(0,0,0,.12)}
.card .photo{left:0;top:0;width:235px;height:222px}
.card .label{position:absolute;left:13px;top:246px;font-size:16px;font-weight:600;color:var(--ink)}
.card .badge{position:absolute;right:8px;top:196px;width:52px;height:52px;border-radius:50%;background:var(--blue);border:3px solid var(--white);display:flex;align-items:center;justify-content:center}
.arrow{position:absolute;width:46px;height:46px;border-radius:50%;border:2px solid var(--ink);display:flex;align-items:center;justify-content:center}
/* contact */
.ci{position:absolute;width:62px;height:62px;border-radius:50%;background:var(--blue);display:flex;align-items:center;justify-content:center}
.ct-title{position:absolute;font-size:17px;font-weight:700;color:var(--ink)}
.ct-text{position:absolute;font-size:16px;line-height:28px;color:var(--text)}
.field{position:absolute;background:var(--white);border:1px solid #9a9a9a;font-size:13px;color:#333;padding:14px 12px}
/* footer */
.ft-h{position:absolute;top:5015px;font-size:18px;font-weight:500;color:var(--white);letter-spacing:1px}
.ft-l{position:absolute;font-size:14px;color:var(--white);line-height:31px}
.soc{position:absolute;top:5115px;width:32px;height:32px;border-radius:50%;background:var(--white)}
</style>
</head>
<body>

<!-- Header -->
<header>
  <div class="abs brand" style="left:112px;top:46px">
    <span class="brand-mark"></span>VELOUR DETAILING
  </div>
  <div class="top-item" style="left:470px">
    <svg width="30" height="30" viewBox="0 0 30 30"><circle cx="15" cy="15" r="13" fill="none" stroke="#151515" stroke-width="2"/><path d="M10 9c1-1 2-1 3 0l1 2-1.5 1.5c.8 1.8 2 3 3.8 3.8L18 15l2 1c1 1 1 2 0 3-3 2-11-5-10-10z" fill="#151515"/></svg>
    1.888.888.8888
  </div>
  <div class="top-item" style="left:638px">
    <svg width="30" height="30" viewBox="0 0 30 30"><circle cx="15" cy="15" r="13" fill="none" stroke="#151515" stroke-width="2"/><rect x="8" y="10" width="14" height="10" fill="none" stroke="#151515" stroke-width="1.8"/><path d="M8 10l7 6 7-6" fill="none" stroke="#151515" stroke-width="1.8"/></svg>
    info@velourdetailing.com
  </div>
  <div class="btn" style="left:893px;top:5px;width:175px;height:47px">CONTACT US</div>
  <div class="btn-tail" style="left:1070px;top:5px;height:47px"></div>
  <nav class="nav">
    <a class="active" style="left:395px">HOME</a>
    <a style="left:475px">ABOUT</a>
    <a style="left:563px">SERVICES</a>
    <a style="left:670px">GALLERY</a>
    <a style="left:773px">CLIENT LOUNGE AREA</a>
    <a style="left:978px">TESTIMONIALS</a>
  </nav>
</header>

<!-- Hero -->
<svg class="abs" style="left:0;top:128px" width="1200" height="630" role="img" aria-label="Dark blue photograph of a luxury car in a studio">
  <defs>
    <linearGradient id="heroGrad" x1="0" y1="0" x2="1" y2="1">
      <stop offset="0" stop-color="#0d3a66"/><stop offset=".6" stop-color="#1a5f98"/><stop offset="1" stop-color="#124a7c"/>
    </linearGradient>
  </defs>
  <polygon points="0,0 1200,0 1200,430 600,572 0,430" fill="url(#heroGrad)"/>
  <polygon points="40,440 600,622 1160,440 600,588" fill="#2a7fc6"/>
</svg>
<h1 class="abs heading center" style="top:205px;font-size:46px;color:var(--white);font-weight:700">PERFECTION, POLISHED.</h1>
<p class="abs center" style="top:284px;font-size:15px;color:var(--white)">Luxury automotive detailing, perfected for those who demand excellence.</p>
<div class="btn" style="left:465px;top:330px;width:228px;height:45px">BOOK YOUR SESSION</div>
<div class="btn-tail" style="left:696px;top:330px;height:45px"></div>

<!-- About -->
<section>
  <div class="abs" style="left:115px;top:820px;width:465px;height:345px;display:flex;align-items:center;justify-content:center">
    <div class="brand" style="font-size:30px;color:var(--navy)"><span class="brand-mark" style="background:var(--navy);width:34px;height:34px"></span>VELOUR</div>
  </div>
  <h2 class="abs heading" style="left:625px;top:810px;font-size:38px">ABOUT US</h2>
  <div class="rule" style="left:632px;top:871px"></div>
  <p class="para" style="left:632px;top:899px;width:430px">Lorem Ipsum is simply dummy text of the printing and typesetting industry. Lorem Ipsum has been the industry's standard dummy text ever since the 1500s, when an unknown printer took a galley of type and scrambled it to make a type specimen book. It has survived not only five centuries, but also the leap into electronic typesetting, remaining essentially unchanged.</p>
  <div class="btn" style="left:637px;top:1132px;width:172px;height:45px">READ MORE</div>
  <div class="btn-tail" style="left:812px;top:1132px;height:45px"></div>
</section>

<!-- Services -->
<svg class="abs" style="left:0;top:0" width="1200" height="1920"><polygon points="0,1330 600,1235 1200,1330 1200,1785 600,1910 0,1785" fill="#dcebf7"/></svg>
<h2 class="abs heading center" style="top:1355px;font-size:38px">OUR SERVICES</h2>
<div class="rule" style="left:560px;top:1422px"></div>
<div class="arrow" style="left:30px;top:1567px"><svg width="22" height="22" viewBox="0 0 22 22"><path d="M18 11H4M10 5l-6 6 6 6" fill="none" stroke="#151515" stroke-width="2"/></svg></div>
<div class="arrow" style="left:1122px;top:1567px"><svg width="22" height="22" viewBox="0 0 22 22"><path d="M4 11h14M12 5l6 6-6 6" fill="none" stroke="#151515" stroke-width="2"/></svg></div>
<div class="card" style="left:110px"><div class="photo" role="img" aria-label="Gloved hand detailing a black car" style="background:linear-gradient(135deg,#3a3d42,#111214)"></div><div class="badge"><svg width="26" height="26" viewBox="0 0 26 26"><path d="M4 17l2-6h14l2 6v4H4z" fill="none" stroke="#fff" stroke-width="2"/></svg></div><div class="label">Car Detailing</div></div>
<div class="card" style="left:358px"><div class="photo" role="img" aria-label="Luxury car interior console" style="background:linear-gradient(135deg,#4a4c50,#121315)"></div><div class="badge"><svg width="26" height="26" viewBox="0 0 26 26"><path d="M4 17l2-6h14l2 6v4H4z" fill="none" stroke="#fff" stroke-width="2"/></svg></div><div class="label">Car Interior</div></div>
<div class="card" style="left:606px"><div class="photo" role="img" aria-label="Polisher applying ceramic coating" style="background:linear-gradient(135deg,#2c2e31,#6a6a60)"></div><div class="badge"><svg width="26" height="26" viewBox="0 0 26 26"><path d="M4 17l2-6h14l2 6v4H4z" fill="none" stroke="#fff" stroke-width="2"/></svg></div><div class="label">Ceramic Coating</div></div>
<div class="card" style="left:854px"><div class="photo" role="img" aria-label="Cleaning an engine bay with a blue cloth" style="background:linear-gradient(135deg,#55585c,#1f2a36)"></div><div class="badge"><svg width="26" height="26" viewBox="0 0 26 26"><path d="M4 17l2-6h14l2 6v4H4z" fill="none" stroke="#fff" stroke-width="2"/></svg></div><div class="label">Engine Bay Cleaning</div></div>

<!-- Gallery -->
<h2 class="abs heading center" style="top:1978px;font-size:38px">OUR GALLERY</h2>
<div class="rule" style="left:560px;top:2047px"></div>
<div class="photo" role="img" aria-label="Microfiber towel wiping a white car" style="left:110px;top:2092px;width:465px;height:270px;background:linear-gradient(135deg,#c9ccd0,#8a8d91)"></div>
<div class="photo" role="img" aria-label="Detailing brush on a car dashboard" style="left:110px;top:2375px;width:255px;height:215px;background:linear-gradient(135deg,#3b3e43,#15171a)"></div>
<div class="photo" role="img" aria-label="Polishing a black bonnet" style="left:375px;top:2375px;width:200px;height:215px;background:linear-gradient(135deg,#2a2b2e,#6b5b40)"></div>
<div class="photo" role="img" aria-label="Headlight of a black car being detailed" style="left:587px;top:2092px;width:251px;height:183px;background:linear-gradient(135deg,#d4d6d8,#202226)"></div>
<div class="photo" role="img" aria-label="Polisher on a lime green car" style="left:587px;top:2285px;width:251px;height:305px;background:linear-gradient(135deg,#b5c94a,#6b7c23)"></div>
<div class="photo" role="img" aria-label="Polishing a dark blue car at night" style="left:848px;top:2092px;width:241px;height:358px;background:linear-gradient(135deg,#1d2433,#4b5262)"></div>
<div class="photo" role="img" aria-label="Gloved hands cleaning an engine" style="left:848px;top:2462px;width:241px;height:128px;background:linear-gradient(135deg,#5b5f64,#2b5d8e)"></div>

<!-- Client lounge -->
<svg class="abs" style="left:0;top:2695px" width="1200" height="730"><polygon points="0,0 1200,0 1200,555 600,725 0,555" fill="#1f78c1"/></svg>
<h2 class="abs heading" style="left:110px;top:2778px;font-size:38px;line-height:50px;color:var(--white)">CLIENT<br>LOUNGE AREA</h2>
<p class="para" style="left:110px;top:2920px;width:430px;color:var(--white)">Lorem Ipsum is simply dummy text of the printing and typesetting industry. Lorem Ipsum has been the industry's standard dummy text ever since the 1500s, when an unknown printer took a galley of type and scrambled it to make a type specimen book. It has survived not only five centuries, but also the leap into electronic typesetting, remaining essentially unchanged.</p>
<div class="btn" style="left:110px;top:3160px;width:180px;height:45px;background:var(--navy)">READ MORE</div>
<div class="btn-tail" style="left:292px;top:3160px;height:45px;background:var(--navy)"></div>
<div class="photo" role="img" aria-label="Lounge chair beside a floor lamp against a textured wall" style="left:622px;top:2773px;width:451px;height:452px;background:linear-gradient(135deg,#3e2e22,#7a5a3e 55%,#2a1f18)"></div>

<!-- Testimonials -->
<h2 class="abs heading center" style="top:3485px;font-size:38px">WHAT OUR CLIENTS SAY</h2>
<div class="rule" style="left:560px;top:3557px"></div>
<div class="arrow" style="left:29px;top:3687px"><svg width="22" height="22" viewBox="0 0 22 22"><path d="M18 11H4M10 5l-6 6 6 6" fill="none" stroke="#151515" stroke-width="2"/></svg></div>
<div class="arrow" style="left:1120px;top:3687px"><svg width="22" height="22" viewBox="0 0 22 22"><path d="M4 11h14M12 5l6 6-6 6" fill="none" stroke="#151515" stroke-width="2"/></svg></div>
<div class="abs" style="left:155px;top:3597px;width:882px;height:248px;background:var(--white);box-shadow:0 2px 10px rgba(0,0,0,.15)"></div>
<div class="photo" role="img" aria-label="Client portrait" style="left:171px;top:3607px;width:226px;height:226px;border-radius:50%;background:radial-gradient(circle at 50% 40%,#e6e2de,#b9b3ad)"></div>
<p class="abs" style="left:437px;top:3628px;width:560px;font-size:13.5px;line-height:26px;color:var(--text)">Lorem Ipsum is simply dummy text of the printing and typesetting industry. Lorem Ipsum has been the industry's standard dummy text ever since the 1500s, when an unknown printer took a galley of type and scrambled it to make a type specimen book.</p>
<div class="abs" style="left:437px;top:3735px;font-size:15px;color:#f0a400;letter-spacing:1px">★★★★★</div>
<div class="abs" style="left:437px;top:3763px;font-size:19px;font-weight:600">Marisa ,</div>
<div class="abs" style="left:437px;top:3800px;font-size:18px;color:#222">Client</div>
<div class="btn" style="left:405px;top:3898px;width:370px;height:47px">READ OUR CLIENT SUCCESS STORIES</div>
<div class="btn-tail" style="left:778px;top:3898px;height:47px"></div>

<!-- Contact & footer backgrounds -->
<div class="abs" style="left:0;top:4700px;width:1200px;height:619px;background:var(--dark)"></div>
<svg class="abs" style="left:0;top:4015px" width="1200" height="890">
  <polygon points="0,685 600,865 1200,685 1200,712 600,888 0,712" fill="#1f78c1"/>
  <polygon points="0,0 1200,0 1200,685 600,865 0,685" fill="#dcebf7"/>
</svg>

<!-- Get in touch -->
<h2 class="abs heading center" style="top:4090px;font-size:38px">GET IN TOUCH</h2>
<div class="ci" style="left:119px;top:4187px"><svg width="28" height="28" viewBox="0 0 28 28"><path d="M14 3a8 8 0 0 0-8 8c0 6 8 14 8 14s8-8 8-14a8 8 0 0 0-8-8z" fill="none" stroke="#fff" stroke-width="2"/><circle cx="14" cy="11" r="3" fill="none" stroke="#fff" stroke-width="2"/></svg></div>
<div class="ct-title" style="left:200px;top:4183px">LOCATION</div>
<div class="ct-text" style="left:200px;top:4210px;width:250px">432, Lorem ipsum is simply dummy text</div>
<div class="ci" style="left:506px;top:4197px"><svg width="28" height="28" viewBox="0 0 28 28"><path d="M8 6c1.5-1.5 3-1.5 4 0l1.5 3-2 2c1 2.5 3 4.5 5.5 5.5l2-2 3 1.5c1.5 1 1.5 2.5 0 4-4 3-17-9-14-14z" fill="none" stroke="#fff" stroke-width="2"/></svg></div>
<div class="ct-title" style="left:582px;top:4190px">CALL</div>
<div class="ct-text" style="left:582px;top:4220px">+1888 888 8888</div>
<div class="ci" style="left:774px;top:4191px"><svg width="28" height="28" viewBox="0 0 28 28"><rect x="6" y="10" width="16" height="13" fill="none" stroke="#fff" stroke-width="2"/><rect x="10" y="4" width="8" height="6" fill="none" stroke="#fff" stroke-width="2"/></svg></div>
<div class="ct-title" style="left:853px;top:4190px">FAX</div>
<div class="ct-text" style="left:853px;top:4220px">info@velourdetailing.com</div>
<div class="abs center" style="top:4278px;font-size:22px;font-weight:600">Inquiries</div>
<div class="abs center" style="top:4323px;font-size:15px;color:var(--text)">For any inquiries or questions, please call: +1888 888 8888 or fill out the following form:</div>
<div class="field" style="left:122px;top:4375px;width:231px;height:55px">First Name</div>
<div class="field" style="left:362px;top:4375px;width:233px;height:55px">Last Name</div>
<div class="field" style="left:122px;top:4440px;width:231px;height:55px">Email Address</div>
<div class="field" style="left:362px;top:4440px;width:233px;height:55px">Phone Number</div>
<div class="field" style="left:122px;top:4507px;width:473px;height:118px">Your Message</div>
<div class="btn" style="left:130px;top:4640px;width:135px;height:45px">SUBMIT</div>
<div class="btn-tail" style="left:268px;top:4640px;height:45px"></div>
<div class="photo" role="img" aria-label="Street map of the studio location" style="left:632px;top:4375px;width:445px;height:285px;border-radius:10px;background:linear-gradient(135deg,#cfe3c9,#e4ecdf 50%,#bcd6bf)"></div>

<!-- Footer -->
<footer>
  <div class="abs brand" style="left:130px;top:5030px;color:var(--white);font-size:20px"><span class="brand-mark" style="background:var(--white)"></span>VELOUR</div>
  <div class="soc" style="left:144px"></div>
  <div class="soc" style="left:187px"></div>
  <div class="soc" style="left:230px"></div>
  <div class="soc" style="left:273px"></div>
  <div class="ft-h" style="left:388px">MAIN LINKS</div>
  <div class="ft-l" style="left:390px;top:5066px">Home<br>About<br>Services<br>Gallery<br>Client Lounge Area<br>Testimonials</div>
  <div class="ft-h" style="left:597px">OTHER LINKS</div>
  <div class="ft-l" style="left:597px;top:5068px">Terms and Conditions<br>Security<br>Privacy Policy</div>
  <div class="ft-h" style="left:860px">NEWSLETTER SIGN UP</div>
  <div class="abs" style="left:860px;top:5060px;font-size:12px;line-height:25px;color:var(--white)">We Will Notify You Of Any<br>Important News</div>
  <div class="abs" style="left:860px;top:5110px;width:170px;height:46px;background:var(--white);font-size:12px;color:#444;padding:16px 10px">Your Email Address</div>
  <div class="abs" style="left:1030px;top:5110px;width:46px;height:46px;background:var(--blue);display:flex;align-items:center;justify-content:center"><svg width="22" height="22" viewBox="0 0 22 22"><path d="M3 11L19 3l-5 16-3-6z M11 13l8-10" fill="none" stroke="#fff" stroke-width="1.6"/></svg></div>
  <div class="abs" style="left:108px;top:5245px;width:977px;height:1px;background:#8a8a8a"></div>
  <div class="abs center" style="top:5268px;font-size:13px;color:var(--white)">© 2025 Velour Detailing I All Rights Reserved</div>
</footer>

</body>
</html>
```